Freelancer Information Security professional needs a business card

I need a simple, young, elegant business card. I'm a freelancer in the InfoSec area and want to be able to give my card to potential customers and new people I meet.

I'd like to have a clean, professional look but at same time not boring or corporate.

The only requirement is to have my "introduction" phrase which is:
"Half hacker, half mercenary."

I have added a card I have as a example, which I think it gives a good example of style I want.

Target Market(s)

Technology / Computers / Engineering

Industry/Entity Type

Information Technology

Contact Information for Business Card

Contact fields I want included:

(351) 93 618 20 54
tomas@vendoza.im
https://vendoza.im

Font styles to use
Sans Serif

Requirements
Nice to have
• Card doesn't need to have a doubled side, but it looks good / fits the design then please do include.
Should not have
• Outdated graphics or images; too much patterns/colors.

```html
<!DOCTYPE html>
<html lang="en">
<head>
<meta charset="utf-8">
<title>Tomas Vendoza — Business Card</title>
<link rel="stylesheet" href="https://fonts.googleapis.com/css2?family=Open+Sans:wght@700&family=Abel&display=swap">
<style>
  :root {
    --page-bg: #e9e6e1;
    --band-top: #2f3788;
    --band-bottom: #2775c4;
    --navy-line: #2e3285;
    --silver-dark: #b9babc;
    --silver-mid: #dcdddf;
    --silver-light: #ffffff;
    --text-dark: #2b2b2f;
    --icon: #3a3f8f;
    --circuit: #8fb0dc;
    --white: #ffffff;
  }
  * { margin: 0; padding: 0; box-sizing: border-box; }
  html, body {
    width: 1200px; height: 952px; overflow: hidden;
    background: var(--page-bg);
  }
  .business-card {
    position: absolute;
    left: 80px; top: 171px;
    width: 1040px; height: 610px;
    overflow: hidden;
    background: linear-gradient(90deg, var(--silver-dark) 0%, var(--silver-mid) 25%, var(--silver-light) 60%, var(--silver-light) 80%, var(--silver-mid) 100%);
    box-shadow: 0 8px 22px rgba(0,0,0,0.18);
  }
  .card-shapes { position: absolute; inset: 0; }
  .identity {
    position: absolute; left: 0; right: 0; top: 0;
    text-align: center; color: var(--white);
    font-family: "Open Sans", sans-serif; font-weight: 700;
  }
  .identity .name {
    position: absolute; left: 0; right: 0; top: 88px;
    font-size: 35px; letter-spacing: 0.5px;
  }
  .identity .tagline {
    position: absolute; left: 0; right: 0; top: 180px;
    font-size: 25px; letter-spacing: 0.6px;
  }
  .circuit-art {
    position: absolute; right: 0; top: 320px;
    width: 230px; height: 290px;
    background: radial-gradient(ellipse at 100% 45%, var(--circuit) 0%, rgba(143,176,220,0.45) 45%, rgba(143,176,220,0) 75%);
    opacity: 0.8;
  }
  .contact-list {
    position: absolute; left: 350px; top: 360px;
    list-style: none;
    font-family: "Abel", sans-serif; font-size: 37px;
    color: var(--text-dark);
  }
  .contact-list li {
    display: flex; align-items: center;
    height: 50px; margin-bottom: 14px;
  }
  .contact-list svg { width: 34px; height: 34px; margin-right: 20px; flex: none; }
</style>
</head>
<body>
  <main class="business-card">
    <svg class="card-shapes" viewBox="0 0 1040 610" width="1040" height="610" aria-hidden="true">
      <defs>
        <linearGradient id="band-fill" x1="0" y1="0" x2="0" y2="1">
          <stop offset="0" stop-color="var(--band-top)"/>
          <stop offset="1" stop-color="var(--band-bottom)"/>
        </linearGradient>
        <linearGradient id="silver-stroke" x1="0" y1="0" x2="1" y2="0">
          <stop offset="0" stop-color="#ffffff"/>
          <stop offset="0.5" stop-color="#9a9ba0"/>
          <stop offset="1" stop-color="#ffffff"/>
        </linearGradient>
      </defs>
      <path class="header-band" d="M0 0 H1040 V238 Q520 322 0 238 Z" fill="url(#band-fill)"/>
      <path class="silver-sweep" d="M0 245 Q520 330 1040 245" fill="none" stroke="url(#silver-stroke)" stroke-width="12"/>
      <path class="navy-sweep" d="M0 258 Q520 340 1040 258" fill="none" stroke="var(--navy-line)" stroke-width="4"/>
    </svg>

    <header class="identity">
      <h1 class="name">TOMAS VENDOZA</h1>
      <p class="tagline">HALF HACKER, HALF MERCENARY.</p>
    </header>

    <div class="circuit-art" role="img" aria-label="Decorative circuit-board traces fading in from the right edge"></div>

    <ul class="contact-list">
      <li>
        <svg viewBox="0 0 34 34"><rect x="10" y="6" width="14" height="22" rx="2" fill="none" stroke="var(--icon)" stroke-width="2.4"/><line x1="14" y1="24" x2="20" y2="24" stroke="var(--icon)" stroke-width="2"/></svg>
        (351) 93 618 20 54
      </li>
      <li>
        <svg viewBox="0 0 34 34"><rect x="3" y="9" width="28" height="17" fill="none" stroke="var(--icon)" stroke-width="2.4"/><polyline points="3,9 17,19 31,9" fill="none" stroke="var(--icon)" stroke-width="2.4"/></svg>
        tomas@vendoza.im
      </li>
      <li>
        <svg viewBox="0 0 34 34"><circle cx="17" cy="17" r="12" fill="none" stroke="var(--icon)" stroke-width="2.4"/><ellipse cx="17" cy="17" rx="5" ry="12" fill="none" stroke="var(--icon)" stroke-width="2"/><line x1="5" y1="17" x2="29" y2="17" stroke="var(--icon)" stroke-width="2"/></svg>
        https://vendoza.im
      </li>
    </ul>
  </main>
</body>
</html>
```